Sonic Vale

Rebrand current website and move it to SonicVale.com. Looking for a professional, eye catching, top 10 in World type website. My current website is: https://madebytorven.sitepadhub.com/sonicvale
I would like it moved to sonicvale.com.

```html
<!DOCTYPE html>
<html lang="en">
<head>
<meta charset="utf-8">
<title>Sonic Vale</title>
<link href="https://fonts.googleapis.com/css2?family=Jost:wght@400;500;600&display=swap" rel="stylesheet">
<style>
:root{
  --ink:#000;
  --paper:#fff;
  --line:#cfcfcf;
  --accent:#116dff;
  --muted:#bdbdbd;
  --panel:rgba(0,0,0,.55);
}
*{box-sizing:border-box;margin:0;padding:0}
html,body{width:1200px;height:4234px;overflow:hidden;background:var(--ink)}
body{position:relative;font-family:"Jost",sans-serif;color:var(--paper)}
.abs{position:absolute}
.backdrop-hero{left:0;top:0;width:1200px;height:822px;background:radial-gradient(ellipse at 50% 30%,#6a6a6a 0%,#3a3a3a 40%,#111 85%,#000 100%)}
.backdrop-studio{left:0;top:1180px;width:1200px;height:800px;background:radial-gradient(ellipse at 30% 60%,#4a4a4a 0%,#262626 45%,#000 90%)}
.backdrop-desk{left:0;top:2050px;width:1200px;height:1150px;background:radial-gradient(ellipse at 55% 45%,#2e3646 0%,#161b25 45%,#000 90%)}
.nav-logo{left:173px;top:34px;font-size:25px;font-weight:600;letter-spacing:.5px}
.nav{left:633px;top:40px;display:flex;gap:24px;font-size:15px;text-transform:uppercase}
.hero-title{left:0;width:1200px;top:208px;text-align:center;font-size:52px;font-weight:500}
.hero-sub{left:0;width:1200px;top:288px;text-align:center;font-size:22px}
.btn-outline{left:542px;top:368px;width:116px;height:51px;border:2px solid var(--paper);display:flex;align-items:center;justify-content:center;font-size:17px}
.section-title{left:0;width:1200px;text-align:center;font-size:34px;font-weight:500;text-transform:uppercase}
.intro{left:173px;top:878px;width:854px;text-align:center;font-size:13.5px;line-height:27px}
.player{left:173px;width:854px;border:1px solid var(--line);background:rgba(0,0,0,.7)}
.cover{left:5px;top:5px;width:138px;height:144px;background:linear-gradient(135deg,#8a5a3a,#c9a24a,#3a5a8a)}
.meta{font-size:13px;line-height:22px}
.tag-btn{background:var(--accent);color:var(--paper);font-size:13px;padding:0 18px;height:44px;display:flex;align-items:center}
.icon-dot{width:32px;height:32px;border-radius:50%;background:var(--paper);display:flex;align-items:center;justify-content:center}
.playlist{left:173px;top:1415px;width:854px;border:1px solid var(--line);background:rgba(0,0,0,.45);list-style:none}
.track{height:48.4px;border-bottom:1px solid #777;display:flex;align-items:center;justify-content:space-between;padding:0 26px 0 24px;font-size:13px}
.track:last-child{border-bottom:none}
.about-title{left:0;width:1200px;top:2250px;text-align:center;font-size:32px;font-weight:500}
.about-sub{left:0;width:1200px;top:2300px;text-align:center;font-size:19px}
.about-text{left:372px;width:456px;top:2355px;text-align:center;font-size:13.5px;line-height:27px}
.btn-solid{background:var(--accent);color:var(--paper);display:flex;align-items:center;justify-content:center}
.card{border:1px solid var(--line);background:var(--panel)}
.card-photo{background:linear-gradient(160deg,#8a8a8a,#3a3a3a 60%,#151515)}
.card-title{font-size:22px;text-transform:uppercase;line-height:32px}
.card-text{font-size:13px;line-height:25px;text-align:justify}
.price{font-size:20px;font-weight:500}
.testimonial{left:173px;top:3311px;width:416px;height:386px;background:var(--paper);color:var(--ink)}
.map{left:610px;top:3311px;width:417px;height:386px;background:linear-gradient(135deg,#e4e4e4,#cfcfcf)}
.contact-title{left:173px;top:3780px;font-size:32px;font-weight:500}
.contact-item{left:173px;display:flex;align-items:center;gap:14px;font-size:14px}
.contact-icon{width:38px;height:38px;border-radius:50%;background:var(--paper);display:flex;align-items:center;justify-content:center}
.field{font-size:14px;border-bottom:1px solid var(--muted);padding:0 0 10px 12px}
.rule{left:173px;top:4131px;width:854px;height:1px;background:var(--muted)}
.copyright{left:0;width:1200px;top:4173px;text-align:center;font-size:13px}
</style>
</head>
<body>
<div class="abs backdrop-hero" role="img" aria-label="Black and white photo of a producer in headphones at a studio desk"></div>
<div class="abs backdrop-studio" role="img" aria-label="Dark photo of a recording studio with keyboards and microphone"></div>
<div class="abs backdrop-desk" role="img" aria-label="Dark photo of hands on a mixing console"></div>

<header>
  <div class="abs nav-logo">SONIC VALE</div>
  <nav class="abs nav"><span>Home</span><span>Shop</span><span>Book Online</span><span>Blog</span><span>Contact</span></nav>
</header>

<section class="hero">
  <h1 class="abs hero-title">TORVEN ASHBY</h1>
  <p class="abs hero-sub">A a Certified Audio Engineer and a beat maker</p>
  <div class="abs btn-outline">READ MORE</div>
</section>

<section class="music">
  <h2 class="abs section-title" style="top:802px">Torven Ashby</h2>
  <p class="abs intro">Intricate but gritty music producer who specializes in all phases of music production.A a Certified Audio Engineer and a beat maker of genres(hip hop,trap,edm,R&amp;B etc..)I think it's most important to take pride in quality sound when your involved in any step of the process of creating! Your Music will be professional mixed and mastered to a industry standard.</p>

  <div class="abs player" style="top:1024px;height:156px">
    <div class="abs cover" role="img" aria-label="Single cover artwork"></div>
    <div class="abs meta" style="left:165px;top:16px">Torven<br>nd<br>FIRST LIGHT (Remastered)</div>
    <svg class="abs" style="left:165px;top:102px" width="80" height="26" viewBox="0 0 80 26"><path d="M2 2 L20 13 L2 24Z" fill="#fff"/><path d="M36 7v12M48 7l-9 6 9 6z" fill="#fff" stroke="#fff" stroke-width="2"/><path d="M58 7l9 6-9 6zM70 7v12" fill="#fff" stroke="#fff" stroke-width="2"/></svg>
    <div class="abs meta" style="left:250px;top:104px">00:00 / 02:09</div>
    <div class="abs tag-btn" style="left:707px;top:20px">Single $200.00</div>
    <div class="abs" style="left:703px;top:102px;display:flex;gap:13px">
      <div class="icon-dot"><svg width="14" height="14" viewBox="0 0 14 14"><path d="M1 5h3l4-3v10L4 9H1z M10 4q3 3 0 6" fill="#116dff" stroke="#116dff"/></svg></div>
      <div class="icon-dot"><svg width="14" height="14" viewBox="0 0 14 14"><path d="M5 2l7-1v9M5 2v9" stroke="#116dff" stroke-width="1.6" fill="none"/><circle cx="4" cy="11" r="2" fill="#116dff"/><circle cx="11" cy="10" r="2" fill="#116dff"/></svg></div>
      <div class="icon-dot"><svg width="14" height="14" viewBox="0 0 14 14"><circle cx="11" cy="3" r="2" fill="#116dff"/><circle cx="3" cy="7" r="2" fill="#116dff"/><circle cx="11" cy="11" r="2" fill="#116dff"/><path d="M11 3L3 7l8 4" stroke="#116dff" fill="none"/></svg></div>
    </div>
  </div>

  <div class="abs player" style="top:1226px;height:173px">
    <svg class="abs" style="left:22px;top:26px" width="104" height="104" viewBox="0 0 104 104"><circle cx="52" cy="52" r="50" fill="none" stroke="#fff" stroke-width="2"/><path d="M41 34 L69 52 L41 70Z" fill="#fff"/></svg>
    <div class="abs meta" style="left:165px;top:18px">Torven<br>Night Shift<br>Loft</div>
    <svg class="abs" style="left:165px;top:108px" width="50" height="16" viewBox="0 0 50 16"><path d="M2 2v12M12 2l-9 6 9 6zM20 2l-8 6 8 6z" fill="#fff" stroke="#fff" stroke-width="1.5"/><path d="M30 2l8 6-8 6zM38 2l8 6-8 6zM48 2v12" fill="#fff" stroke="#fff" stroke-width="1.5"/></svg>
    <div class="abs" style="left:228px;top:115px;width:436px;height:3px;background:#fff"></div>
    <div class="abs meta" style="left:670px;top:105px">00:00 / 04:16</div>
    <div class="abs icon-dot" style="left:771px;top:104px;width:24px;height:24px"><svg width="12" height="12" viewBox="0 0 14 14"><path d="M1 5h3l4-3v10L4 9H1z" fill="#116dff"/></svg></div>
    <div class="abs icon-dot" style="left:805px;top:104px;width:24px;height:24px"><svg width="12" height="12" viewBox="0 0 14 14"><circle cx="5" cy="11" r="2" fill="#116dff"/><path d="M6 11V2l6-1v8" stroke="#116dff" fill="none"/></svg></div>
    <div class="abs icon-dot" style="left:801px;top:38px"><svg width="14" height="14" viewBox="0 0 14 14"><circle cx="11" cy="3" r="2" fill="#116dff"/><circle cx="3" cy="7" r="2" fill="#116dff"/><circle cx="11" cy="11" r="2" fill="#116dff"/><path d="M11 3L3 7l8 4" stroke="#116dff" fill="none"/></svg></div>
  </div>

  <ol class="abs playlist">
    <li class="track"><span>1.&nbsp;&nbsp; Night Shift / Torven</span><svg width="12" height="12" viewBox="0 0 14 14"><circle cx="11" cy="3" r="2" fill="#fff"/><circle cx="3" cy="7" r="2" fill="#fff"/><circle cx="11" cy="11" r="2" fill="#fff"/><path d="M11 3L3 7l8 4" stroke="#fff" fill="none"/></svg></li>
    <li class="track"><span>2.&nbsp;&nbsp; Top Shelf / Torven</span><svg width="12" height="12" viewBox="0 0 14 14"><circle cx="11" cy="3" r="2" fill="#fff"/><circle cx="3" cy="7" r="2" fill="#fff"/><circle cx="11" cy="11" r="2" fill="#fff"/><path d="M11 3L3 7l8 4" stroke="#fff" fill="none"/></svg></li>
    <li class="track"><span>3.&nbsp;&nbsp; Vapor / Torven</span><svg width="12" height="12" viewBox="0 0 14 14"><circle cx="11" cy="3" r="2" fill="#fff"/><circle cx="3" cy="7" r="2" fill="#fff"/><circle cx="11" cy="11" r="2" fill="#fff"/><path d="M11 3L3 7l8 4" stroke="#fff" fill="none"/></svg></li>
    <li class="track"><span>4.&nbsp;&nbsp; Low End / Torven</span><svg width="12" height="12" viewBox="0 0 14 14"><circle cx="11" cy="3" r="2" fill="#fff"/><circle cx="3" cy="7" r="2" fill="#fff"/><circle cx="11" cy="11" r="2" fill="#fff"/><path d="M11 3L3 7l8 4" stroke="#fff" fill="none"/></svg></li>
    <li class="track"><span>5.&nbsp;&nbsp; Low End / Torven</span><svg width="12" height="12" viewBox="0 0 14 14"><circle cx="11" cy="3" r="2" fill="#fff"/><circle cx="3" cy="7" r="2" fill="#fff"/><circle cx="11" cy="11" r="2" fill="#fff"/><path d="M11 3L3 7l8 4" stroke="#fff" fill="none"/></svg></li>
    <li class="track"><span>6.&nbsp;&nbsp; static / Torven</span><svg width="12" height="12" viewBox="0 0 14 14"><circle cx="11" cy="3" r="2" fill="#fff"/><circle cx="3" cy="7" r="2" fill="#fff"/><circle cx="11" cy="11" r="2" fill="#fff"/><path d="M11 3L3 7l8 4" stroke="#fff" fill="none"/></svg></li>
    <li class="track"><span>7.&nbsp;&nbsp; the drive / Torven</span><svg width="12" height="12" viewBox="0 0 14 14"><circle cx="11" cy="3" r="2" fill="#fff"/><circle cx="3" cy="7" r="2" fill="#fff"/><circle cx="11" cy="11" r="2" fill="#fff"/><path d="M11 3L3 7l8 4" stroke="#fff" fill="none"/></svg></li>
    <li class="track"><span>8.&nbsp;&nbsp; Shore to Shore / Torven</span><svg width="12" height="12" viewBox="0 0 14 14"><circle cx="11" cy="3" r="2" fill="#fff"/><circle cx="3" cy="7" r="2" fill="#fff"/><circle cx="11" cy="11" r="2" fill="#fff"/><path d="M11 3L3 7l8 4" stroke="#fff" fill="none"/></svg></li>
    <li class="track"><span>9.&nbsp;&nbsp; keep Moving / Torven</span><svg width="12" height="12" viewBox="0 0 14 14"><circle cx="11" cy="3" r="2" fill="#fff"/><circle cx="3" cy="7" r="2" fill="#fff"/><circle cx="11" cy="11" r="2" fill="#fff"/><path d="M11 3L3 7l8 4" stroke="#fff" fill="none"/></svg></li>
    <li class="track"><span>10.&nbsp;&nbsp; LuLu / Torven</span><svg width="12" height="12" viewBox="0 0 14 14"><circle cx="11" cy="3" r="2" fill="#fff"/><circle cx="3" cy="7" r="2" fill="#fff"/><circle cx="11" cy="11" r="2" fill="#fff"/><path d="M11 3L3 7l8 4" stroke="#fff" fill="none"/></svg></li>
  </ol>
</section>

<section class="about">
  <svg class="abs" style="left:0;top:1990px" width="1200" height="700" viewBox="0 0 1200 700">
    <path d="M600 12 L937 351 L600 690 L263 351Z" fill="none" stroke="#fff" stroke-width="2"/>
    <path d="M600 42 L695 137 L600 232 L505 137Z" fill="#fff"/>
  </svg>
  <div class="abs" role="img" aria-label="Portrait of the producer" style="left:522px;top:2049px;width:156px;height:156px;transform:rotate(45deg) scale(.83);background:linear-gradient(135deg,#b89a80,#5a4a40 60%,#2a2420)"></div>
  <h2 class="abs about-title">ABOUT</h2>
  <p class="abs about-sub">A Life Steeped in Sound</p>
  <p class="abs about-text">Hailing from Port Calder, Torven has always pushed himself to achieve more success in his music career. Looking to perfect his technical abilities and develop his own unique style, Torven draws upon his Port Calder roots and lifelong passion for music. Get in touch to learn more about his background, experience, and latest projects.</p>
  <div class="abs btn-solid" style="left:539px;top:2520px;width:122px;height:45px;font-size:17px;font-weight:500">Get In Touch</div>
  <svg class="abs" style="left:588px;top:2628px" width="24" height="26" viewBox="0 0 24 26" fill="none" stroke="#fff" stroke-width="2"><path d="M2 3l10 9 10-9M2 11l10 9 10-9"/></svg>
</section>

<section class="services">
  <h2 class="abs section-title" style="top:2774px">My Music</h2>

  <div class="abs card" style="left:173px;top:2874px;width:448px;height:352px">
    <div class="abs card-photo" role="img" aria-label="Studio microphone close-up" style="left:8px;top:8px;width:200px;height:334px"></div>
    <div class="abs card-title" style="left:231px;top:26px;width:190px">Mixing and Mastering</div>
    <p class="abs card-text" style="left:231px;top:104px;width:199px">Hailing from Port Calder, Torven has always pushed himself to achieve more success in his music career. Looking to perfect his tech nical abilities and develop his own unique style.</p>
    <div class="abs btn-solid" style="left:231px;top:274px;width:105px;height:38px;font-size:15px">Buy Now</div>
  </div>

  <div class="abs card" style="left:635px;top:2874px;width:392px;height:169px">
    <div class="abs card-photo" role="img" aria-label="Studio control room with monitors" style="left:7px;top:7px;width:173px;height:155px;background:linear-gradient(160deg,#6a5a50,#3a3230 60%,#1a1818)"></div>
    <div class="abs card-title" style="left:197px;top:18px;font-size:20px">Book a Session</div>
    <div class="abs price" style="left:197px;top:62px">$120.00</div>
    <div class="abs btn-solid" style="left:197px;top:102px;width:82px;height:34px;font-size:13px">Buy Now</div>
  </div>

  <div class="abs card" style="left:635px;top:3058px;width:392px;height:169px">
    <div class="abs card-photo" role="img" aria-label="Producer at a desk with screens" style="left:7px;top:7px;width:173px;height:155px;background:linear-gradient(160deg,#3a2030,#2a1a2a 55%,#101018)"></div>
    <div class="abs card-title" style="left:197px;top:18px;font-size:20px">Book a Session</div>
    <div class="abs price" style="left:197px;top:62px">$120.00</div>
    <div class="abs btn-solid" style="left:197px;top:102px;width:82px;height:34px;font-size:13px">Buy Now</div>
  </div>
</section>

<section class="testimonials">
  <div class="abs testimonial">
    <h3 class="abs" style="left:22px;top:48px;font-size:27px;font-weight:500">OUR TESTIMONIALS</h3>
    <div class="abs" style="left:18px;top:100px;font-size:130px;font-weight:600;line-height:1">&ldquo;</div>
    <p class="abs" style="left:22px;top:230px;width:380px;font-size:17px;line-height:30px">&ldquo;Music expresses that which cannot be said and on which it is impossible to be silent&rdquo;</p>
    <p class="abs" style="left:22px;top:306px;font-size:15px">- Marcel Dorne</p>
  </div>
  <div class="abs map" role="img" aria-label="Street map showing the studio location"></div>
</section>

<section class="contact">
  <h2 class="abs contact-title">CONTACT US</h2>
  <div class="abs contact-item" style="top:3854px"><span class="contact-icon"><svg width="18" height="20" viewBox="0 0 18 20" fill="none" stroke="#000" stroke-width="1.6"><path d="M9 19s7-7 7-11A7 7 0 0 0 2 8c0 4 7 11 7 11z"/><circle cx="9" cy="8" r="2.5"/></svg></span>Port Calder,Marlowe</div>
  <div class="abs contact-item" style="top:3922px"><span class="contact-icon"><svg width="18" height="14" viewBox="0 0 18 14" fill="none" stroke="#000" stroke-width="1.6"><rect x="1" y="1" width="16" height="12"/><path d="M1 1l8 7 8-7"/></svg></span>producedbytorven@mailbox.com</div>
  <div class="abs contact-item" style="top:3989px"><span class="contact-icon"><svg width="16" height="16" viewBox="0 0 16 16" fill="none" stroke="#000" stroke-width="1.6"><path d="M3 1l3 3-2 2q2 4 6 6l2-2 3 3-2 2Q6 14 1 3z"/></svg></span>555-014-2290</div>

  <div class="abs field" style="left:554px;top:3790px;width:223px">Name</div>
  <div class="abs field" style="left:794px;top:3790px;width:233px">Email</div>
  <div class="abs field" style="left:554px;top:3857px;width:223px">Phone</div>
  <div class="abs field" style="left:794px;top:3857px;width:233px">Address</div>
  <div class="abs field" style="left:554px;top:3915px;width:473px;height:67px">Type your message here...</div>
  <div class="abs btn-solid" style="left:554px;top:4011px;width:104px;height:46px;font-size:16px;font-weight:500">Submit</div>
</section>

<footer>
  <div class="abs rule"></div>
  <p class="abs copyright">Copyrights &copy; 2021 Sonic Vale. All Rights Reserved.</p>
</footer>
</body>
</html>
```